TA BRAMLEY BUSINESS CARD DESIGN PROJECT

We need to utilize our logo that was expertly created on PixelHarbor and now need to match this with a business card design.

```html
<!DOCTYPE html>
<html lang="en">
<head>
<meta charset="utf-8">
<title>TA Bramley Business Card</title>
<link href="https://fonts.googleapis.com/css2?family=Montserrat:wght@400;500;700&display=swap" rel="stylesheet">
<style>
  :root {
    --page-bg: #d9d4cc;
    --card-bg: #ecedef;
    --brand-blue: #1f4d84;
    --card-text-light: #f1f1f1;
  }
  * { margin: 0; padding: 0; box-sizing: border-box; }
  html, body {
    width: 1200px;
    height: 1200px;
    overflow: hidden;
    background: var(--page-bg);
    font-family: "Montserrat", Arial, sans-serif;
  }
  .canvas {
    position: relative;
    width: 1200px;
    height: 1200px;
  }
  .business-card {
    position: absolute;
    left: 60px;
    top: 305px;
    width: 1080px;
    height: 590px;
    border-radius: 28px;
    background: var(--card-bg);
    overflow: hidden;
    box-shadow: 0 10px 30px rgba(0,0,0,0.12);
  }
  .card-band {
    position: absolute;
    inset: 0;
    width: 1080px;
    height: 590px;
  }
  .brand-name {
    position: absolute;
    left: 62px;
    top: 150px;
    font-weight: 700;
    font-size: 62px;
    letter-spacing: 3px;
    color: var(--brand-blue);
    line-height: 1;
  }
  .person {
    position: absolute;
    right: 50px;
    top: 58px;
    text-align: right;
    color: var(--brand-blue);
  }
  .person-name {
    font-weight: 700;
    font-size: 36px;
    letter-spacing: 0.5px;
    line-height: 1;
  }
  .person-title {
    margin-top: 14px;
    font-weight: 500;
    font-size: 24px;
    line-height: 1;
  }
  .address {
    position: absolute;
    right: 50px;
    top: 334px;
    text-align: right;
    color: var(--card-text-light);
    font-size: 25px;
    line-height: 38px;
  }
  .contact-list {
    position: absolute;
    right: 50px;
    top: 430px;
    list-style: none;
    color: var(--card-text-light);
    font-size: 25px;
  }
  .contact-item {
    display: flex;
    justify-content: flex-end;
    align-items: center;
    gap: 10px;
    height: 39px;
  }
  .contact-icon {
    width: 22px;
    height: 22px;
    fill: var(--card-text-light);
  }
</style>
</head>
<body>
<div class="canvas">
  <div class="business-card">
    <svg class="card-band" viewBox="0 0 1080 590" aria-hidden="true">
      <path fill="var(--brand-blue)" d="M0,520 C300,560 560,330 1080,200 L1080,590 L0,590 Z"/>
    </svg>

    <div class="brand-name">TA BRAMLEY</div>

    <div class="person">
      <div class="person-name">MARCUS DELANEY</div>
      <div class="person-title">President</div>
    </div>

    <div class="address">
      <div>1187 Coral Bay Drive</div>
      <div>Seacliff CA 90000</div>
    </div>

    <ul class="contact-list">
      <li class="contact-item">
        <span>555-314-2790</span>
        <svg class="contact-icon" viewBox="0 0 24 24" aria-label="Phone"><path d="M6.6 10.8a15.1 15.1 0 0 0 6.6 6.6l2.2-2.2a1 1 0 0 1 1-.25 11.4 11.4 0 0 0 3.6.57 1 1 0 0 1 1 1V20a1 1 0 0 1-1 1A17 17 0 0 1 3 4a1 1 0 0 1 1-1h3.5a1 1 0 0 1 1 1c0 1.25.2 2.45.57 3.57a1 1 0 0 1-.25 1z"/></svg>
      </li>
      <li class="contact-item">
        <span>m.delaney@tabramley.com</span>
        <svg class="contact-icon" viewBox="0 0 24 24" aria-label="Email"><path d="M3 5h18v2l-9 6-9-6z M3 9l9 6 9-6v10H3z"/></svg>
      </li>
      <li class="contact-item">
        <span>www.tabramley.com</span>
        <svg class="contact-icon" viewBox="0 0 24 24" aria-label="Website"><circle cx="12" cy="12" r="9" fill="none" stroke="var(--card-text-light)" stroke-width="2"/><path d="M3 12h18 M12 3c3 3 3 15 0 18 M12 3c-3 3-3 15 0 18" fill="none" stroke="var(--card-text-light)" stroke-width="1.6"/></svg>
      </li>
    </ul>
  </div>
</div>
</body>
</html>
```